Corvane Capital Business Cards

These are professional business cards that are for my family office.
Put fake emails and phone numbers as of now until I finalize those components. This family office controls my families investments, assets, and future. The cards should be professional.
..
.
.
.
I just uploaded another variation of a logo I would like to see as a business card to I am inbeteen which logo to use

Target Market(s)

business

Industry/Entity Type

business

Contact Information for Business Card

Professional, wealth related, finance related.

Requirements
Must have
• Logo

```html
<!DOCTYPE html>
<html lang="en">
<head>
<meta charset="UTF-8">
<title>Corvane Capital — Business Cards</title>
<link rel="stylesheet" href="https://fonts.googleapis.com/css2?family=Playfair+Display:wght@400&family=EB+Garamond:wght@400;500&display=swap">
<style>
  :root {
    --backdrop: #3b3b3b;
    --card: #232323;
    --card-edge: #4a4a4a;
    --gold: #c6ad6c;
    --ivory: #f4f2ec;
  }
  * { box-sizing: border-box; margin: 0; padding: 0; }
  html, body {
    width: 1200px;
    height: 694px;
    overflow: hidden;
    background: var(--backdrop);
  }
  .sheet {
    position: relative;
    width: 1200px;
    height: 694px;
    display: flex;
    align-items: center;
    justify-content: center;
    gap: 40px;
  }
  .card {
    position: relative;
    width: 540px;
    height: 310px;
    background: var(--card);
    border: 1px solid var(--card-edge);
    box-shadow: 0 18px 40px rgba(0,0,0,0.45);
  }

  /* Wordmark */
  .wordmark {
    display: flex;
    align-items: center;
    gap: 14px;
    font-family: "Playfair Display", serif;
    font-weight: 400;
    color: var(--gold);
    letter-spacing: 0.08em;
    text-transform: uppercase;
    white-space: nowrap;
  }
  .wordmark__square {
    background: var(--gold);
    flex: none;
  }

  /* Front */
  .card--front {
    display: flex;
    align-items: center;
    justify-content: center;
  }
  .card--front .wordmark { font-size: 40px; }
  .card--front .wordmark__square { width: 22px; height: 22px; }

  /* Back */
  .card--back .wordmark {
    position: absolute;
    left: 120px;
    top: 64px;
    font-size: 30px;
  }
  .card--back .wordmark__square { width: 16px; height: 16px; }

  .holder {
    position: absolute;
    left: 60px;
    top: 140px;
    width: 200px;
    text-align: right;
    font-family: "EB Garamond", serif;
  }
  .holder__name {
    font-size: 24px;
    color: var(--gold);
    line-height: 1.1;
  }
  .holder__role {
    font-size: 15px;
    color: var(--ivory);
    margin-top: 2px;
  }

  .divider {
    position: absolute;
    left: 282px;
    top: 128px;
    width: 1px;
    height: 76px;
    background: linear-gradient(to bottom, rgba(198,173,108,0), var(--gold) 40%, rgba(198,173,108,0));
  }

  .contacts {
    position: absolute;
    left: 302px;
    top: 126px;
    list-style: none;
    font-family: "EB Garamond", serif;
    font-size: 15px;
    color: var(--ivory);
  }
  .contacts__item {
    display: flex;
    align-items: center;
    gap: 10px;
    height: 26px;
  }
  .contacts__icon {
    width: 16px;
    height: 16px;
    flex: none;
  }

  .address {
    position: absolute;
    left: 0;
    right: 0;
    bottom: 40px;
    text-align: center;
    font-family: "EB Garamond", serif;
    font-size: 16px;
    color: var(--ivory);
    letter-spacing: 0.01em;
  }
</style>
</head>
<body>
  <main class="sheet">
    <section class="card card--front" aria-label="Business card front">
      <div class="wordmark">
        <span class="wordmark__square"></span>
        <span class="wordmark__name">Corvane Capital</span>
      </div>
    </section>

    <section class="card card--back" aria-label="Business card back">
      <div class="wordmark">
        <span class="wordmark__square"></span>
        <span class="wordmark__name">Corvane Capital</span>
      </div>

      <div class="holder">
        <p class="holder__name">Elliot Marsh</p>
        <p class="holder__role">Owner</p>
      </div>

      <span class="divider"></span>

      <ul class="contacts">
        <li class="contacts__item">
          <svg class="contacts__icon" viewBox="0 0 16 16" aria-hidden="true">
            <circle cx="8" cy="8" r="8" fill="var(--gold)"/>
            <path d="M5 4.2l1.6-.4.9 2-1 .8a5 5 0 0 0 2.4 2.4l.8-1 2 .9-.4 1.6c-3.6.2-6.5-2.7-6.3-6.3z" fill="var(--card)"/>
          </svg>
          <span>044-987 650 312</span>
        </li>
        <li class="contacts__item">
          <svg class="contacts__icon" viewBox="0 0 16 16" aria-hidden="true">
            <rect x="1" y="3.5" width="14" height="9" fill="var(--gold)"/>
            <path d="M1 3.5l7 5 7-5" fill="none" stroke="var(--card)" stroke-width="1.2"/>
          </svg>
          <span>info@corvanemail.com</span>
        </li>
        <li class="contacts__item">
          <svg class="contacts__icon" viewBox="0 0 16 16" aria-hidden="true">
            <circle cx="8" cy="8" r="7.5" fill="var(--gold)"/>
            <g fill="none" stroke="var(--card)" stroke-width="1">
              <circle cx="8" cy="8" r="5"/>
              <ellipse cx="8" cy="8" rx="2.2" ry="5"/>
              <path d="M3 8h10"/>
            </g>
          </svg>
          <span>www.corvanecapital.com</span>
        </li>
      </ul>

      <p class="address">118, Harbour Lane Suite 4 30917, Country name</p>
    </section>
  </main>
</body>
</html>
```